Fall Convention Graphic Designs (logo, digital brochure, t-shirt designs, social media templates)

I need a graphic package for the Redwick Movement Guild Autumn Dance Convention. Redwick Movement Guild is a non-profit organization of dance teachers, and this educational dance conference is for members and their students with multiple events throughout the weekend. The convention has a new them each year. I will need a package with a general "logo" type graphic, a digital brochure, t-shirt design, and social media graphic templates. This year's Convention has a general theme and names for each event throughout the weekend.
The theme and event names for this year are:
Convention Theme Twice Around a Waltz: Beneath the Harlow Moons
Registration Desk The Willowgate Nook
Members Welcome A Moonwashed Greeting
Banquet A Velvet Twilight
President's Reception Glow Beyond Dusk
Jr. Member Desk Wanderers' Wharf
Jr. Member Pizza Party Cricket Mixer
Members Luncheon Harlow Reveries

I am attaching a word file that includes information and text to be included in brochure. Also attached are designs from previous years for brochures, T-shirts, and social media graphics.

Colors that we will be using for decorations at various events over the weekend this year are shades of green (fern and mossy green), shades of blue (including navy), white, and pinks (including mauve). The banquet event will be decorated as an enchanted forest. We are using fairy lights, books that look like a storybook, and lanterns for decorations as well. I think I would like a more modern design, and I do not want anything that is childish or too whimsical. While we are using floral decorations I don't want bunches of flowers in the design.

*I am open to seeing initial logo type designs and giving feedback to make sure it is a direction that I like and then moving forward with the other parts of the project.

```html
<!DOCTYPE html>
<html lang="en">
<head>
<meta charset="utf-8">
<title>Redwick Movement Guild Autumn Dance Convention – Brochure</title>
<link rel="stylesheet" href="https://fonts.googleapis.com/css2?family=Cinzel:wght@400;500;600&family=Noto+Serif:ital,wght@0,400;0,700;1,400;1,700&family=Pinyon+Script&display=swap">
<style>
  :root{
    --board:#53636b;
    --night:#1e2b36;
    --night-deep:#141e27;
    --moss:#3a4a3a;
    --cream:#f2ecdc;
    --paper:#f8f7f1;
    --mist:#e6e9e3;
    --fern:#2d5e4f;
    --fern-text:#1f5b4a;
    --navy:#17425e;
    --ink:#1d1d1d;
    --sat-fill:#e8ebe5;
    --sun-fill:#e3e7ea;
    --leaf:#4e8a3a;
    --pill:#223826;
    --pill-edge:#d8cf8a;
  }
  *{margin:0;padding:0;box-sizing:border-box}
  html,body{width:1200px;height:873px;overflow:hidden;background:var(--board)}
  .canvas{position:relative;width:1200px;height:873px}
  .page{position:absolute;top:66px;width:524px;height:740px;overflow:hidden}

  /* Cover */
  .cover{left:72px;color:var(--cream);text-align:center}
  .cover-scene{position:absolute;inset:0;
    background:radial-gradient(ellipse at 30% 55%,#5b5a45 0%,#3b4436 25%,transparent 55%),
               radial-gradient(ellipse at 75% 80%,#3c4a44 0%,transparent 50%),
               linear-gradient(180deg,var(--night-deep) 0%,var(--night) 45%,#2c3a3e 75%,#3a4440 100%)}
  .cover-content{position:absolute;inset:0}
  .abs{position:absolute;left:0;right:0}
  .brand-main{top:22px;font-family:'Cinzel',serif;font-size:35px;letter-spacing:2px;line-height:1}
  .brand-sub{top:60px;font-family:'Cinzel',serif;font-size:20px;letter-spacing:1px;line-height:1}
  .brand-season{top:88px;font-family:'Cinzel',serif;font-size:13px;letter-spacing:1px;line-height:1}
  .title-script{top:118px;font-family:'Pinyon Script',cursive;font-size:70px;line-height:78px}
  .subtitle{top:290px;font-family:'Cinzel',serif;font-size:21px;letter-spacing:.5px}
  .dates{top:336px;font-family:'Cinzel',serif;font-size:20px}
  .venues{top:368px;font-family:'Noto Serif',serif;font-weight:700;font-size:15.5px;line-height:20px}
  .rule{position:absolute;left:51px;width:422px;height:1px;background:var(--cream);opacity:.85}
  .intensive{top:460px;font-family:'Cinzel',serif;font-size:21.5px;letter-spacing:.3px}
  .stay{top:510px;font-family:'Noto Serif',serif;font-size:15px;line-height:22px}
  .stay strong{font-size:18px}
  .stay em{display:block;margin-top:8px;font-size:15px;line-height:18px}
  .phone{font-weight:700;font-size:18px;display:block;margin-top:4px}
  .booking{position:absolute;left:91px;top:678px;width:343px;height:41px;border-radius:21px;background:var(--pill);border:1.5px solid var(--pill-edge);
    display:flex;align-items:center;justify-content:center;gap:10px;font-family:'Noto Serif',serif;font-size:15.5px}

  /* Schedule page */
  .schedule{left:605px;background:var(--paper);color:var(--ink);font-family:'Noto Serif',serif}
  .top-band{position:absolute;left:0;top:0;width:524px;height:223px;background:var(--mist)}
  .section-title{position:absolute;left:0;right:0;text-align:center;font-family:'Cinzel',serif;font-weight:500;font-size:22px;color:var(--fern-text);letter-spacing:.5px}
  .names-table{position:absolute;left:21px;top:54px;width:342px;height:158px;background:var(--paper);border-collapse:collapse;font-size:9px}
  .names-table th{background:var(--fern);color:#fff;font-family:'Cinzel',serif;font-weight:500;font-size:11px;text-align:left;height:26px;padding-left:13px}
  .names-table td{padding:0 0 0 13px;line-height:12.3px;vertical-align:top}
  .names-table tr.first td{padding-top:14px}
  .names-table td.name{padding-left:0}
  .lantern-art{position:absolute;left:363px;top:57px;width:161px;height:180px;
    background:radial-gradient(circle at 55% 48%,#f0a33a 0%,#8a4a22 18%,#4f6a3a 32%,rgba(106,170,70,.55) 55%,rgba(232,236,228,0) 75%)}
  .ivy-corner{position:absolute;left:0;top:686px;width:150px;height:54px;
    background:radial-gradient(ellipse at 10% 90%,rgba(92,160,60,.85) 0%,rgba(120,180,80,.45) 40%,rgba(248,247,241,0) 75%)}
  .day{position:absolute;left:21px;font-family:'Cinzel',serif;font-weight:500;font-size:11.5px;color:var(--ink)}
  .label{position:absolute;left:21px;font-style:italic;font-weight:700;font-size:11px}
  .item{position:absolute;left:21px;font-size:9px;display:flex;align-items:center;gap:5px}
  .item.plain{left:36px}
  .day-box{position:absolute;left:21px;width:481px}
  .day-box.sat{top:444px;height:145px;background:var(--sat-fill)}
  .day-box.sun{top:601px;height:119px;background:var(--sun-fill)}
  .day-head{height:27px;color:#fff;display:flex;align-items:center;justify-content:center;font-family:'Cinzel',serif;font-size:11.5px;gap:4px}
  .sat .day-head{background:var(--fern)}
  .sun .day-head{background:var(--navy)}
  .day-head em{font-family:'Noto Serif',serif;font-size:10px}
  .times{margin:12px 0 0 13px;font-size:9px;line-height:12.3px;border-collapse:collapse}
  .times td{vertical-align:top;padding:0}
  .times td.time{width:79px}
  .times td.what{width:390px}
</style>
</head>
<body>
<div class="canvas">

  <section class="page cover">
    <div class="cover-scene" role="img" aria-label="Moonlit enchanted garden with a stone archway, hanging lanterns and ivy-covered steps"></div>
    <div class="cover-content">
      <div class="abs brand-main">REDWICK</div>
      <div class="abs brand-sub">MOVEMENT GUILD</div>
      <div class="abs brand-season">AUTUMN CONVENTION</div>
      <h1 class="abs title-script">Twice Around a<br>Waltz</h1>
      <div class="abs subtitle">BENEATH THE HARLOW MOONS</div>
      <div class="abs dates">NOVEMBER 19 – 22, 2026</div>
      <div class="abs venues">Halden Convention Center<br>Marlowe Grand Hotel<br>Ashbury, NC</div>
      <div class="rule" style="top:449px"></div>
      <div class="abs intensive">TEACHER'S INTENSIVE ON FRIDAY</div>
      <div class="rule" style="top:495px"></div>
      <div class="abs stay">
        Outstanding accommodations at the<br>
        <strong>Marlowe Grand Hotel</strong><br>
        4470 Lanternway Boulevard, Ashbury, NC 27999
        <em>Call for reservations and mention RMG<br>for your best rate!</em>
        <span class="phone">555-014-2270 or book online.</span>
      </div>
      <div class="booking">
        <svg width="22" height="22" viewBox="0 0 24 24" fill="none" stroke="#f2ecdc" stroke-width="1.6" aria-hidden="true">
          <circle cx="12" cy="12" r="10"/><ellipse cx="12" cy="12" rx="4.5" ry="10"/><line x1="2" y1="12" x2="22" y2="12"/><line x1="4" y1="7" x2="20" y2="7"/><line x1="4" y1="17" x2="20" y2="17"/>
        </svg>
        https://book.stayline.example/event/
      </div>
    </div>
  </section>

  <section class="page schedule">
    <div class="top-band"></div>
    <h2 class="section-title" style="top:18px">CONVENTION THEME &amp; EVENT NAMES</h2>
    <table class="names-table">
      <thead><tr><th style="width:119px">EVENT</th><th>NAME</th></tr></thead>
      <tbody>
        <tr class="first"><td>Convention Theme</td><td class="name">Twice Around a Waltz: Beneath the Harlow Moons</td></tr>
        <tr><td>Registration Desk</td><td class="name">The Willowgate Nook</td></tr>
        <tr><td>Members Welcome</td><td class="name">A Moonwashed Greeting</td></tr>
        <tr><td>Banquet</td><td class="name">A Velvet Twilight</td></tr>
        <tr><td>President's Reception</td><td class="name">Glow Beyond Dusk</td></tr>
        <tr><td>Jr. Member Desk</td><td class="name">Wanderers' Wharf</td></tr>
        <tr><td>Jr. Member Pizza Party</td><td class="name">Cricket Mixer</td></tr>
        <tr><td>Members Luncheon</td><td class="name" style="height:100%">Harlow Reveries</td></tr>
      </tbody>
    </table>
    <div class="lantern-art" role="img" aria-label="Glowing vintage lantern wrapped in green ivy"></div>

    <h2 class="section-title" style="top:236px">SCHEDULE OF EVENTS</h2>

    <div class="day" style="top:266px">THURSDAY, NOVEMBER 19TH</div>
    <div class="item" style="top:288px"><svg width="10" height="10" viewBox="0 0 10 10" aria-hidden="true"><path d="M1 9 C1 4 4 1 9 1 C9 6 6 9 1 9Z" fill="var(--leaf)"/></svg>Solo Title Scholarship Competition Audition Classes, Interviews, and Opening Number Rehearsals</div>
    <div class="item" style="top:303px"><svg width="10" height="10" viewBox="0 0 10 10" aria-hidden="true"><path d="M1 9 C1 4 4 1 9 1 C9 6 6 9 1 9Z" fill="var(--leaf)"/></svg><span><em>A Moonwashed Greeting</em>– Members Welcome Party</span></div>

    <div class="day" style="top:327px">FRIDAY, NOVEMBER 20TH</div>
    <div class="label" style="top:346px">Teachers Intensive</div>
    <div class="item" style="top:365px"><svg width="10" height="10" viewBox="0 0 10 10" aria-hidden="true"><path d="M1 9 C1 4 4 1 9 1 C9 6 6 9 1 9Z" fill="var(--leaf)"/></svg>Solo Title Scholarship Competition Audition Classes, Interviews, and Opening Number Rehearsals</div>
    <div class="label" style="top:384px">Registration Packet Pickup</div>
    <div class="item" style="top:404px"><svg width="10" height="10" viewBox="0 0 10 10" aria-hidden="true"><path d="M1 9 C1 4 4 1 9 1 C9 6 6 9 1 9Z" fill="var(--leaf)"/></svg>Solo Title Scholarship Competition and Crowning</div>
    <div class="item plain" style="top:416px"><span><em>Cricket Mixer</em> - Jr. Members Pizza and Pajama Party</span></div>

    <div class="day-box sat">
      <div class="day-head">SATURDAY, NOVEMBER 21ST - <em>Marlowe Grand Hotel, Halden Convention Center</em></div>
      <table class="times">
        <tr><td class="time">8:00am</td><td class="what">The Willowgate Nook&nbsp; Registration Desk Opens</td></tr>
        <tr><td class="time">8:00am</td><td class="what">Wanderers' Wharf&nbsp; Junior Member Desk Opens</td></tr>
        <tr><td class="time">8:00am-8:45am</td><td class="what">Junior Member Banquet Performance Rehearsal</td></tr>
        <tr><td class="time">9:00am-1:00pm</td><td class="what">Convention Classes&nbsp; Mini</td></tr>
        <tr><td class="time">9:00am-3:00pm</td><td class="what">Convention Classes&nbsp;&nbsp; Junior | Senior | Teachers &amp; Assistants</td></tr>
        <tr><td class="time">6:00pm-7:30pm</td><td class="what">Banquet – A Velvet Twilight</td></tr>
        <tr><td class="time">8:30pm</td><td class="what">Miss and Mr. Talent and Crowning</td></tr>
        <tr><td class="time">10:00pm</td><td class="what"><em>Glow Beyond Dusk</em> - President's Reception (Immediately following Miss / Mr. Dance Crowning)</td></tr>
      </table>
    </div>

    <div class="day-box sun">
      <div class="day-head">SUNDAY, NOVEMBER 22ND - <em>Marlowe Grand Hotel, Halden Convention Center</em></div>
      <table class="times">
        <tr><td class="time">7:30am</td><td class="what">Contract Signing for New Title Holders</td></tr>
        <tr><td class="time">8:00am-9:00am</td><td class="what">Judges Critiques for New Title Holders</td></tr>
        <tr><td class="time">9:00am-1:00pm</td><td class="what">Convention Classes&nbsp;&nbsp; Mini | Junior | Senior | Teachers &amp; Assistants</td></tr>
        <tr><td class="time">1:00pm-2:00pm</td><td class="what">Junior Member Special Class</td></tr>
        <tr><td class="time">1:00pm</td><td class="what"><em>Harlow Reveries</em>– Members Luncheon (Must be Pre-Registered)</td></tr>
        <tr><td class="time">2:00pm</td><td class="what">Grand Body Meeting</td></tr>
      </table>
    </div>

    <div class="ivy-corner" role="img" aria-label="Trailing ivy leaves along the lower corner"></div>
  </section>

</div>
</body>
</html>
```